professional business card design for technology company

We are a small technology consulting firm, specialising in consulting based around Cloud and Managed services. Our colour scheme is yellow, blue and white, as you can see in the logos. Although we are based in melbourne australia, due to the nature of our work, our clients can be located anywhere. We are looking for a clean, professional, positive look - similar to our company logo

Target Market(s)

small business

Industry/Entity Type

Business

Contact Information for Business Card

eye catching, designed to incorporate some level of raised printing. Must contain website address, phone number, name and job title

Requirements
Must have
• Logo (attached) - use of the same colour scheme

```html
<!DOCTYPE html>
<html lang="en">
<head>
<meta charset="utf-8">
<title>Nimbara Business Card</title>
<link rel="stylesheet" href="https://fonts.googleapis.com/css2?family=Exo+2:wght@400;500;700&display=swap">
<style>
  :root {
    --backdrop: #e6e6e6;
    --card: #ffffff;
    --card-shade: #f1f1f1;
    --band: #5a5a5a;
    --accent-blue: #35a8e0;
    --ink: #444444;
    --ink-light: #ffffff;
  }
  * { margin: 0; padding: 0; box-sizing: border-box; }
  html, body {
    width: 1200px; height: 900px; overflow: hidden;
    background: var(--backdrop);
    font-family: "Exo 2", sans-serif;
  }
  .card {
    position: absolute; left: 100px; top: 165px;
    width: 1000px; height: 570px;
    background: linear-gradient(160deg, var(--card) 40%, var(--card-shade));
    box-shadow: 0 12px 30px rgba(0,0,0,0.18);
    overflow: hidden;
  }
  .card-swoosh { position: absolute; inset: 0; width: 100%; height: 100%; }
  .brand {
    position: absolute; left: 90px; top: 190px;
    display: flex; align-items: center; gap: 26px;
  }
  .brand-mark {
    width: 64px; height: 64px; border-radius: 50%;
    background: var(--accent-blue);
  }
  .brand-name {
    font-weight: 700; font-size: 92px; letter-spacing: -1px;
    color: var(--ink); line-height: 1;
  }
  .contact {
    position: absolute; right: 60px; top: 46px;
    text-align: right;
  }
  .contact-name {
    font-weight: 500; font-size: 30px; letter-spacing: 3px;
    color: var(--accent-blue);
  }
  .contact-role {
    font-size: 22px; color: var(--ink); letter-spacing: 1px;
    margin-bottom: 22px;
  }
  .contact-list { list-style: none; }
  .contact-item {
    display: flex; justify-content: flex-end; align-items: center; gap: 12px;
    font-size: 19px; color: var(--ink); letter-spacing: 1.5px;
    height: 32px;
  }
  .contact-icon { width: 20px; height: 20px; flex: none; }
  .address {
    position: absolute; left: 44px; bottom: 26px;
    font-size: 24px; line-height: 1.3; letter-spacing: 1.5px;
    color: var(--ink-light);
  }
</style>
</head>
<body>
  <div class="card">
    <svg class="card-swoosh" viewBox="0 0 1000 570" preserveAspectRatio="none" aria-hidden="true">
      <path d="M560,430 C760,380 900,300 1000,205 L1000,228 C905,318 765,396 560,430 Z" fill="var(--accent-blue)"/>
      <path d="M0,478 C380,470 760,400 1000,250 L1000,570 L0,570 Z" fill="var(--band)"/>
    </svg>

    <div class="brand">
      <span class="brand-mark"></span>
      <span class="brand-name">Nimbara</span>
    </div>

    <div class="contact">
      <p class="contact-name">LIAM CARTER</p>
      <p class="contact-role">Managing Director</p>
      <ul class="contact-list">
        <li class="contact-item">013 456 7890
          <svg class="contact-icon" viewBox="0 0 20 20" aria-label="Phone"><path d="M5 2 L8 2 L9 6 L7 8 C8 11 9 12 12 13 L14 11 L18 12 L18 15 C18 17 16 18 14 18 C8 17 3 12 2 6 C2 4 3 2 5 2 Z" fill="var(--accent-blue)"/></svg>
        </li>
        <li class="contact-item">013 456 7891
          <svg class="contact-icon" viewBox="0 0 20 20" aria-label="Mobile"><rect x="5" y="1.5" width="10" height="17" rx="2" fill="none" stroke="var(--accent-blue)" stroke-width="2"/></svg>
        </li>
        <li class="contact-item">013 456 7892
          <svg class="contact-icon" viewBox="0 0 20 20" aria-label="Fax"><rect x="5" y="2" width="10" height="6" fill="var(--accent-blue)"/><rect x="2" y="9" width="16" height="9" rx="1.5" fill="var(--accent-blue)"/></svg>
        </li>
        <li class="contact-item">hello@nimbara.net
          <svg class="contact-icon" viewBox="0 0 20 20" aria-label="Email"><rect x="2" y="4" width="16" height="12" rx="1.5" fill="var(--accent-blue)"/><path d="M2.5 5 L10 11 L17.5 5" fill="none" stroke="#fff" stroke-width="1.5"/></svg>
        </li>
        <li class="contact-item">www.nimbara.net
          <svg class="contact-icon" viewBox="0 0 20 20" aria-label="Website"><circle cx="10" cy="10" r="8" fill="var(--accent-blue)"/><path d="M2 10 H18 M10 2 C6 6 6 14 10 18 M10 2 C14 6 14 14 10 18" fill="none" stroke="#fff" stroke-width="1.2"/></svg>
        </li>
      </ul>
    </div>

    <p class="address">045: 12th floor, Park<br>Harbour Road MLB</p>
  </div>
</body>
</html>
```